Heritage Hollow Business Cards

Require a business card design. <br/><br/>Needs to include logo (either round or long version) plus these details:<br/>Maya Torvell<br/>Heritage Hollow<br/>maya@kelvadtrading.com.au<br/>02 6481 7395<br/>PO Box Glenwarra NSW 2791<br/>www.heritagehollow.com.au<br/><br/>I need in an editable format so that I can create for multiple staff members. <br/><br/>

Target Market(s)

We are an online store selling renovation products to home owners are builders. Looking for a classic classy design.

Industry/Entity Type

Home And Garden

Contact Information for Business Card

Maya Torvell
Heritage Hollow
maya@kelvadtrading.com.au
02 6481 7395
PO Box Glenwarra NSW 2791
www.heritagehollow.com.au

Colors

Designer to choose colors to be used in the design.

Requirements
Must have
• Must include Logo.

```html
<!DOCTYPE html>
<html lang="en">
<head>
<meta charset="utf-8">
<title>Heritage Hollow Business Cards</title>
<link rel="stylesheet" href="https://fonts.googleapis.com/css2?family=Raleway:wght@400;500;600&display=swap">
<style>
  :root {
    --brand-green: #00c585;
    --card-light: #eeeeee;
    --ink: #1d1d1f;
    --backdrop: #e2e2e2;
    --white: #ffffff;
  }
  * { margin: 0; padding: 0; box-sizing: border-box; }
  html, body {
    width: 1200px;
    height: 1200px;
    overflow: hidden;
    background: var(--backdrop);
    font-family: "Raleway", sans-serif;
  }
  .canvas { position: relative; width: 1200px; height: 1200px; }

  .card { position: absolute; left: 260px; width: 679px; height: 441px; }
  .card--front { top: 104px; background: var(--brand-green); }
  .card--back { top: 617px; background: var(--card-light); }

  .front-brand {
    position: absolute;
    left: 220px;
    top: 225px;
    display: flex;
    align-items: center;
    gap: 18px;
  }
  .front-brand__dot {
    width: 40px; height: 40px;
    border: 1.5px solid var(--white);
    border-radius: 50%;
    flex: none;
  }
  .front-brand__name {
    color: var(--white);
    font-weight: 600;
    font-size: 40px;
    line-height: 40px;
  }

  .back-brand {
    position: absolute;
    left: 30px;
    top: 163px;
    display: flex;
    align-items: center;
    gap: 14px;
  }
  .back-brand__dot {
    width: 30px; height: 30px;
    border: 1.5px solid var(--ink);
    border-radius: 50%;
    flex: none;
  }
  .back-brand__name {
    color: var(--ink);
    font-weight: 600;
    font-size: 40px;
    line-height: 44px;
    white-space: nowrap;
  }

  .person {
    position: absolute;
    left: 377px;
    top: 80px;
    width: 226px;
  }
  .person__name {
    font-weight: 500;
    font-size: 48px;
    line-height: 52px;
    color: var(--ink);
    white-space: nowrap;
    text-align: right;
    border-bottom: 1.5px solid var(--brand-green);
    padding-bottom: 3px;
  }
  .person__role {
    margin-top: 7px;
    font-size: 14px;
    letter-spacing: 6px;
    color: var(--ink);
  }

  .contacts {
    position: absolute;
    right: 76px;
    top: 206px;
    list-style: none;
  }
  .contact {
    display: flex;
    align-items: center;
    justify-content: flex-end;
    gap: 10px;
    height: 30px;
    margin-bottom: 14px;
    font-size: 20px;
    color: var(--ink);
    white-space: nowrap;
  }
  .contact__icon { width: 30px; height: 30px; flex: none; }
</style>
</head>
<body>
<main class="canvas">
  <section class="card card--front">
    <div class="front-brand">
      <span class="front-brand__dot"></span>
      <span class="front-brand__name">Heritage<br>Hollow</span>
    </div>
  </section>

  <section class="card card--back">
    <div class="back-brand">
      <span class="back-brand__dot"></span>
      <span class="back-brand__name">Heritage Hollow</span>
    </div>

    <div class="person">
      <h1 class="person__name">Maya Torvell</h1>
      <p class="person__role">Director</p>
    </div>

    <ul class="contacts">
      <li class="contact">
        <span>02 6481 7395</span>
        <svg class="contact__icon" viewBox="0 0 30 30" aria-hidden="true">
          <circle cx="15" cy="15" r="15" fill="var(--brand-green)"/>
          <path d="M10 8.5c1-.6 1.8-.4 2.3.4l1.3 2.2c.4.7.2 1.4-.4 1.8l-.9.6c.6 1.7 2 3.3 3.9 4.1l.6-.9c.4-.6 1.1-.8 1.8-.4l2.2 1.3c.8.5 1 1.3.4 2.3-.9 1.5-2.5 1.9-4.1 1.2-3.5-1.5-6.3-4.3-7.8-7.8-.7-1.6-.3-3.3 1.2-4.1z" fill="var(--white)"/>
        </svg>
      </li>
      <li class="contact">
        <span>maya@kelvadtrading.com.au</span>
        <svg class="contact__icon" viewBox="0 0 30 30" aria-hidden="true">
          <circle cx="15" cy="15" r="15" fill="var(--brand-green)"/>
          <circle cx="15" cy="15" r="3.2" fill="none" stroke="var(--white)" stroke-width="2"/>
          <path d="M18.2 13v3.2c0 1.4 2.6 1.6 2.6-1.2a5.8 5.8 0 1 0-2.3 4.6" fill="none" stroke="var(--white)" stroke-width="2" stroke-linecap="round"/>
        </svg>
      </li>
      <li class="contact">
        <span>www.heritagehollow.com.au</span>
        <svg class="contact__icon" viewBox="0 0 30 30" aria-hidden="true">
          <circle cx="15" cy="15" r="15" fill="var(--brand-green)"/>
          <g fill="none" stroke="var(--white)" stroke-width="1.6">
            <circle cx="15" cy="15" r="7.5"/>
            <ellipse cx="15" cy="15" rx="3.2" ry="7.5"/>
            <line x1="7.5" y1="15" x2="22.5" y2="15"/>
            <line x1="15" y1="7.5" x2="15" y2="22.5"/>
          </g>
        </svg>
      </li>
      <li class="contact">
        <span>PO Box Glenwarra NSW 2791</span>
        <svg class="contact__icon" viewBox="0 0 30 30" aria-hidden="true">
          <path d="M15 1C7.8 1 2 6.6 2 13.6 2 21.5 15 29 15 29s13-7.5 13-15.4C28 6.6 22.2 1 15 1z" fill="var(--brand-green)"/>
          <path d="M15 7a5 5 0 0 0-5 5c0 3.6 5 8.5 5 8.5s5-4.9 5-8.5a5 5 0 0 0-5-5z" fill="var(--white)"/>
          <circle cx="15" cy="12" r="1.8" fill="var(--brand-green)"/>
        </svg>
      </li>
    </ul>
  </section>
</main>
</body>
</html>
```